Brimlow OrthoLink IT Inc. new website

i need a website for my company which is dedicated to installation and service of computer systems in Dental Offices. I would like for it to encompass a technology feel and professional look. The company deals with all aspects of technology like, Audio Visual, computer systems and networks, Cloud services like data backup, data center. We provide manage services, support and services to Dental Professionals.
Updates

Looking for a Technology font but professional look Added Wednesday, April 20, 2016

Target Market(s)

Dental, Dentist

Industry/Entity Type

Dental

Number of Pages Required

5+ page

Font styles to use
Other font styles liked:
• Futuristic or Techy

Colors
0255a3
ec1f27

Requirements
Must have
• Tabs
Nice to have
• Have no idea maybe some suggestion on your part may help
Should not have
• A professional feel but have a techy look

```html
<!DOCTYPE html>
<html lang="en">
<head>
<meta charset="utf-8">
<title>Brimlow OrthoLink IT</title>
<link rel="stylesheet" href="https://fonts.googleapis.com/css2?family=Roboto:wght@300;400;500;700&display=swap">
<style>
:root{
  --blue:#0255a3;
  --red:#ec1f27;
  --ink:#333333;
  --muted:#8a8a8a;
  --panel:#efefef;
  --band:#eeeeee;
  --footer:#333333;
  --white:#ffffff;
}
*{box-sizing:border-box;margin:0;padding:0}
html,body{width:1200px;height:2691px;overflow:hidden}
body{position:relative;background:var(--white);font-family:'Roboto',Arial,sans-serif;color:var(--ink)}
.abs{position:absolute}

.hero-photo{left:0;top:0;width:1200px;height:678px;background:linear-gradient(110deg,#d9dde3 0%,#eef1f4 35%,#c9d3df 60%,#5b7fb8 85%,#e9ecf0 100%)}

.site-header{left:77px;top:14px;width:1046px;height:104px;background:var(--white);border-bottom:4px solid var(--red)}
.brand{position:absolute;left:14px;top:32px;font-size:27px;font-weight:700;color:var(--blue);letter-spacing:-.3px}
.main-nav{position:absolute;top:44px;left:0;width:100%;font-size:16px;color:#444}
.main-nav span{position:absolute;white-space:nowrap}
.main-nav .active{color:var(--blue)}
.nav-pointer{position:absolute;left:365px;top:100px}

.services{left:77px;top:556px;width:1046px;height:395px}
.service{position:absolute;top:40px;width:348px;text-align:center}
.service .icon{width:94px;height:94px;margin:0 auto;border:2px solid var(--red);background:var(--white);display:flex;align-items:center;justify-content:center}
.service .icon.solid{background:var(--red)}
.service h3{margin-top:28px;font-size:19px;font-weight:400;color:var(--blue);line-height:25px;height:50px;padding:0 50px}
.service p{margin-top:10px;font-size:14px;line-height:23px;color:var(--muted);padding:0 60px}
.service .more{margin-top:14px}
.divider{position:absolute;top:32px;width:1px;height:255px;background:#dddddd}

.welcome{left:0;top:1010px;width:1200px;text-align:center}
.section-title{font-size:40px;font-weight:400;color:var(--blue);letter-spacing:-.3px}
.section-title em{font-style:normal;color:var(--red)}
.welcome p{width:860px;margin:22px auto 0;font-size:15px;line-height:25px;color:var(--muted)}

.testimonial{left:77px;top:1207px;width:1046px;height:208px;background:var(--panel);border-left:4px solid var(--red)}
.avatar{position:absolute;left:44px;top:46px;width:116px;height:116px;border-radius:50%;border:4px solid var(--white);background:radial-gradient(circle at 50% 45%,#d8c4b4,#8a7a70)}
.testimonial blockquote{position:absolute;left:200px;top:70px;width:760px;font-size:15px;line-height:24px;color:#444}
.client{position:absolute;right:60px;top:165px;font-size:15px;color:var(--blue)}
.client small{font-size:15px;color:#444}
.arrows{position:absolute;right:12px;top:167px}

.blog-title{left:0;top:1470px;width:1200px;text-align:center}
.card{position:absolute;top:1555px;width:249px}
.card .thumb{width:249px;height:167px;border:1px solid #cfd9e4}
.card .date{margin-top:22px;font-size:16px;color:var(--red)}
.card h4{margin-top:23px;font-size:15px;font-weight:400;line-height:23px;color:#444}
.card p{margin-top:10px;font-size:14px;line-height:22px;color:var(--muted)}
.btn{display:inline-block;background:var(--red);color:var(--white);font-size:20px;text-align:center}
.card .btn{position:absolute;top:370px;left:0;width:162px;height:56px;line-height:56px}

.support{left:0;top:2045px;width:1200px;height:291px;background:var(--band)}
.support .copy{position:absolute;left:0;top:30px;width:994px;text-align:center}
.support h2{font-size:40px;font-weight:400;color:var(--blue)}
.support h2 em{font-style:normal;color:var(--red)}
.support .lead{margin-top:14px;font-size:22px;color:#555}
.support .reach{margin-top:12px;font-size:18px;color:#555}
.support .reach b{font-weight:400;color:var(--red)}
.support .btn{position:absolute;left:400px;top:187px;width:194px;height:61px;line-height:61px}
.support-person{position:absolute;left:897px;top:41px;width:197px;height:250px;background:linear-gradient(180deg,#e2c7b3 0%,#b99a86 30%,#4a4d55 60%,#2f3138 100%);border-radius:90px 90px 0 0}

.site-footer{left:0;top:2336px;width:1200px;height:292px;background:var(--footer);color:#bbbbbb}
.col{position:absolute;top:44px}
.col h5{font-size:19px;font-weight:400;color:var(--white)}
.post{position:relative;margin-top:32px;height:58px}
.post + .post{margin-top:30px}
.post .pic{position:absolute;left:0;top:0;width:54px;height:54px;border-radius:50%;border:2px solid #ddd;background:linear-gradient(135deg,#b49a80,#5d5a4e)}
.post .when{position:absolute;left:71px;top:0;font-size:16px;color:var(--white)}
.post .text{position:absolute;left:71px;top:24px;width:230px;font-size:13.5px;line-height:21px;color:#bbb}
.contact-line{position:relative;padding-left:42px;font-size:14px;line-height:20px;color:#bbb}
.contact-line svg{position:absolute;left:0;top:0}
.contact-line .lbl{color:#ccc}
.news p{margin-top:26px;width:300px;font-size:14px;line-height:22px}
.signup{position:absolute;left:0;top:152px;width:332px;height:52px;display:flex}
.signup .field{width:219px;background:#f4f4f4;color:#999;font-size:13px;line-height:52px;padding-left:14px}
.signup .go{width:113px;background:var(--red);color:var(--white);font-size:16px;line-height:52px;text-align:center}

.legal{left:0;top:2628px;width:1200px;height:63px;background:var(--red);color:#222;font-size:14px;text-align:center;line-height:63px}
.legal b{font-weight:400;color:var(--white)}
</style>
</head>
<body>

<div class="abs hero-photo" role="img" aria-label="Photo of a dental professional in blue scrubs thinking in front of a computer monitor"></div>

<header class="abs site-header">
  <div class="brand">Brimlow OrthoLink IT</div>
  <nav class="main-nav">
    <span class="active" style="left:347px">HOME</span>
    <span style="left:440px">ABOUT</span>
    <span style="left:533px">SERVICES</span>
    <span style="left:657px">SUPPORT</span>
    <span style="left:776px">CLIENT</span>
    <span style="left:880px">BLOG</span>
    <span style="left:968px">CONTACT</span>
  </nav>
  <svg class="nav-pointer" width="20" height="10" viewBox="0 0 20 10"><path d="M0 0 L10 10 L20 0Z" fill="#ec1f27"/></svg>
</header>

<section class="abs services">
  <svg class="abs" style="left:0;top:0" width="1046" height="395" viewBox="0 0 1046 395"><path d="M0 0 H1046 V323 L523 395 L0 323Z" fill="#efefef"/></svg>
  <div class="divider" style="left:345px"></div>
  <div class="divider" style="left:700px"></div>
  <div class="service" style="left:0">
    <div class="icon solid"><svg width="52" height="40" viewBox="0 0 52 40"><rect x="4" y="4" width="44" height="30" rx="4" fill="#fff"/><rect x="9" y="9" width="34" height="20" fill="#0255a3"/></svg></div>
    <h3>AUDIO VISUAL</h3>
    <p>Lorem Ipsum is simply dummy text of the printing and typesetting industry. Lorem Ipsum has been the</p>
    <div class="more"><svg width="12" height="12" viewBox="0 0 12 12"><path d="M2 1l4 4 4-4M2 6l4 4 4-4" stroke="#ec1f27" stroke-width="2" fill="none"/></svg></div>
  </div>
  <div class="service" style="left:349px">
    <div class="icon"><svg width="56" height="44" viewBox="0 0 56 44"><rect x="8" y="4" width="40" height="26" fill="none" stroke="#0255a3" stroke-width="3"/><path d="M20 38h16M28 30v8" stroke="#0255a3" stroke-width="3"/><rect x="2" y="20" width="12" height="18" fill="none" stroke="#777" stroke-width="2"/></svg></div>
    <h3>COMPUTER SYSTEMS AND NETWORKS</h3>
    <p>Lorem Ipsum is simply dummy text of the printing and typesetting industry. Lorem Ipsum has been the</p>
    <div class="more"><svg width="12" height="12" viewBox="0 0 12 12"><path d="M2 1l4 4 4-4M2 6l4 4 4-4" stroke="#ec1f27" stroke-width="2" fill="none"/></svg></div>
  </div>
  <div class="service" style="left:698px">
    <div class="icon"><svg width="56" height="44" viewBox="0 0 56 44"><path d="M16 22a8 8 0 0 1 4-15 11 11 0 0 1 20 3 7 7 0 0 1 0 12Z" fill="#dbe6f2" stroke="#0255a3" stroke-width="2"/><rect x="6" y="28" width="18" height="12" fill="none" stroke="#777" stroke-width="2"/><rect x="32" y="28" width="18" height="12" fill="none" stroke="#777" stroke-width="2"/></svg></div>
    <h3>CLOUD SERVICES OF DATA BACKUP</h3>
    <p>Lorem Ipsum is simply dummy text of the printing and typesetting industry. Lorem Ipsum has been the</p>
    <div class="more"><svg width="12" height="12" viewBox="0 0 12 12"><path d="M2 1l4 4 4-4M2 6l4 4 4-4" stroke="#ec1f27" stroke-width="2" fill="none"/></svg></div>
  </div>
</section>

<section class="abs welcome">
  <h1 class="section-title">WELCOME TO <em>BRIMLOW ORTHOLINK IT</em></h1>
  <p>Lorem Ipsum is simply dummy text of the printing and typesetting industry. Lorem Ipsum has been the industry's standard dummy text ever since the 1500s, when an unknown printer took a galley of type and scrambled it to make a type specimen book. It has survived not only five centuries, but also the leap into electronic typesetting.</p>
</section>

<section class="abs testimonial">
  <div class="avatar" role="img" aria-label="Portrait of a support agent wearing a headset"></div>
  <blockquote>" Lorem Ipsum is simply dummy text of the printing and typesetting industry. Lorem Ipsum has been the industry's standard dummy text ever since the 1500s, when an unknown printer took a galley of type and scrambled it to make a type specimen book. It has survived "</blockquote>
  <div class="client">CLIENT NAME <small>(something.com)</small></div>
  <svg class="arrows" width="28" height="14" viewBox="0 0 28 14"><path d="M8 1 L2 7 L8 13" stroke="#555" stroke-width="2" fill="none"/><path d="M20 1 L26 7 L20 13" stroke="#ec1f27" stroke-width="2" fill="none"/></svg>
</section>

<h2 class="abs blog-title section-title">LATEST <em>BLOG</em></h2>

<article class="card" style="left:77px">
  <div class="thumb" role="img" aria-label="Photo of a support agent with a headset holding a tablet" style="background:linear-gradient(135deg,#f1f1f1,#c9c5c0)"></div>
  <div class="date">April 21</div>
  <h4>LOREM IPSUM SIMPLE DUMMTY TEXT FOR TYPE</h4>
  <p>Lorem ipsum is simple dummy text of the writting and typesetting industry</p>
  <span class="btn">READ MORE</span>
</article>
<article class="card" style="left:343px">
  <div class="thumb" role="img" aria-label="Photo of two smiling dental professionals in a clinic" style="background:linear-gradient(135deg,#e8edf2,#b8c2cc)"></div>
  <div class="date">April 21</div>
  <h4>LOREM IPSUM SIMPLE DUMMTY TEXT FOR TYPE</h4>
  <p>Lorem ipsum is simple dummy text of the writting and typesetting industry</p>
  <span class="btn">READ MORE</span>
</article>
<article class="card" style="left:608px">
  <div class="thumb" role="img" aria-label="Photo of technicians with headsets working at computers in a blue-lit office" style="background:linear-gradient(135deg,#a8d4ec,#2a7ab4)"></div>
  <div class="date">April 21</div>
  <h4>LOREM IPSUM SIMPLE DUMMTY TEXT FOR TYPE</h4>
  <p>Lorem ipsum is simple dummy text of the writting and typesetting industry</p>
  <span class="btn">READ MORE</span>
</article>
<article class="card" style="left:874px">
  <div class="thumb" role="img" aria-label="Photo of a dentist in a white coat standing in a treatment room" style="background:linear-gradient(135deg,#f2f4f6,#c8d2dc)"></div>
  <div class="date">April 21</div>
  <h4>LOREM IPSUM SIMPLE DUMMTY TEXT FOR TYPE</h4>
  <p>Lorem ipsum is simple dummy text of the writting and typesetting industry</p>
  <span class="btn">READ MORE</span>
</article>

<section class="abs support">
  <div class="copy">
    <h2>SUPPORT <em>WITH US</em></h2>
    <div class="lead">Got unanswered questions? We are Ready to Help You</div>
    <div class="reach"><b>Email</b> : info@brimlowortholink.com | <b>Call:</b> +(91) 555 010 2468</div>
  </div>
  <span class="btn">CONTACT NOW</span>
  <div class="support-person" role="img" aria-label="Photo of a smiling businesswoman in a grey suit"></div>
</section>

<footer class="abs site-footer">
  <div class="col" style="left:81px">
    <h5>LATEST BLOG</h5>
    <div class="post"><div class="pic" role="img" aria-label="Blog thumbnail photo"></div><div class="when">21/4</div><div class="text">Lorem ipsum dolor sit amet, consectetur adipiscing elit, sed do.</div></div>
    <div class="post"><div class="pic" role="img" aria-label="Blog thumbnail photo"></div><div class="when">21/4</div><div class="text">Lorem ipsum dolor sit amet, consectetur adipiscing elit, sed do.</div></div>
  </div>
  <div class="col" style="left:436px">
    <h5>KEEP IN TOUCH</h5>
    <div class="contact-line" style="margin-top:30px"><svg width="20" height="24" viewBox="0 0 20 24"><path d="M10 22s7-8 7-13a7 7 0 0 0-14 0c0 5 7 13 7 13Z" fill="none" stroke="#ec1f27" stroke-width="2"/><circle cx="10" cy="9" r="2.5" fill="none" stroke="#ec1f27" stroke-width="2"/></svg><span class="lbl">BRIMLOW ORTHOLINK IT</span><br>Lorem ipsum dolor amet simple.</div>
    <div class="contact-line" style="margin-top:20px"><svg width="20" height="20" viewBox="0 0 20 20"><path d="M4 2l4 1 1 4-2 2a11 11 0 0 0 4 4l2-2 4 1 1 4-3 2C8 18 2 12 1 5Z" fill="none" stroke="#bbb" stroke-width="1.5"/></svg>+(91) 555 010 2468</div>
    <div class="contact-line" style="margin-top:20px"><svg width="20" height="20" viewBox="0 0 20 20"><rect x="5" y="2" width="10" height="5" fill="none" stroke="#bbb" stroke-width="1.5"/><rect x="2" y="7" width="16" height="7" fill="none" stroke="#bbb" stroke-width="1.5"/><rect x="5" y="12" width="10" height="6" fill="none" stroke="#bbb" stroke-width="1.5"/></svg>+(91) 555 010 2468</div>
    <div class="contact-line" style="margin-top:20px"><svg width="20" height="20" viewBox="0 0 20 20"><rect x="2" y="4" width="16" height="12" fill="none" stroke="#bbb" stroke-width="1.5"/><path d="M2 4l8 7 8-7" fill="none" stroke="#bbb" stroke-width="1.5"/></svg>info@brimlowortholink.com</div>
  </div>
  <div class="col news" style="left:791px">
    <h5>SUBCRIBE TO NEWSLETTER</h5>
    <p>Lorem Ipsum is simply dummy text of the printing and typesetting..</p>
    <div class="signup"><div class="field">Enter your Email*</div><div class="go">SUBSCRIBE</div></div>
  </div>
</footer>

<div class="abs legal">© 2016 <b>BRIMLOW ORTHOLINK IT</b> All rights reserved.</div>

</body>
</html>
```